Wordpress Design for a Private Label BBQ Brand

For our new brand, we'd need a new Wordpress website. We'd prefer to run the website on Wordpress

We'd like to include the following
- space for description of the brand
- space for product portfolio (not a shop!)
- space for socials
- space for support
- space for contact

```html
<!DOCTYPE html>
<html lang="en">
<head>
<meta charset="utf-8">
<title>Ardento – BBQ</title>
<link href="https://fonts.googleapis.com/css2?family=Cinzel:wght@600;700&family=Catamaran:wght@400;500;600;700&display=swap" rel="stylesheet">
<style>
:root{
  --orange:#ec6a1f;
  --red:#c8202a;
  --ink:#1a1a1a;
  --grey:#f0f0f0;
  --dark:#0b0b0b;
  --white:#fff;
  --serif:'Cinzel',serif;
  --sans:'Catamaran',sans-serif;
}
*{box-sizing:border-box;margin:0;padding:0}
html,body{width:1200px;height:3120px;overflow:hidden}
body{position:relative;font-family:var(--sans);color:var(--ink);background:var(--white)}
.abs{position:absolute}
.center{left:0;width:1200px;text-align:center}

/* top bar */
.topbar{top:0;left:0;width:1200px;height:63px;background:var(--red);color:#fff;font-weight:700;font-size:16px}
.topbar .left{position:absolute;left:0;top:0;height:63px;width:425px;background:var(--orange);clip-path:polygon(0 0,100% 0,92% 100%,0 100%)}
.topbar .item{position:absolute;top:0;height:63px;display:flex;align-items:center;gap:10px}
.ring{width:30px;height:30px;border:2px solid #fff;border-radius:50%;display:inline-flex;align-items:center;justify-content:center}
.ring svg{width:15px;height:15px;fill:#fff}
.ring.sm{width:28px;height:28px}

/* header */
.header{top:63px;left:0;width:1200px;height:85px}
.brand{position:absolute;left:111px;top:20px;display:flex;align-items:center;gap:10px;font-family:var(--serif);font-weight:700;font-size:38px;color:var(--ink)}
.brand .dot{width:24px;height:24px;background:var(--red);border-radius:50%}
.nav a{position:absolute;top:31px;font-family:var(--serif);font-size:14px;font-weight:600;color:var(--ink);text-decoration:none}
.nav a.active{color:var(--orange);border-bottom:2px solid var(--orange)}
.btn{display:flex;align-items:center;justify-content:center;font-family:var(--serif);font-weight:700;text-decoration:none;border-radius:26px 0 26px 0}
.btn-cta{position:absolute;left:953px;top:17px;width:136px;height:51px;background:linear-gradient(90deg,var(--orange),var(--red));color:#fff;font-size:15px}

/* hero */
.hero{top:148px;left:0;width:1200px;height:454px;background:radial-gradient(ellipse 50% 35% at 55% 68%,#e06a1a 0%,#8a3310 35%,#1c1a1a 70%,#0e0e0e 100%)}
.hero h1{position:absolute;top:44px;font-family:var(--serif);font-size:58px;font-weight:700;color:#fff;letter-spacing:1px}
.hero p{position:absolute;top:116px;font-size:16px;font-weight:600;color:#fff;line-height:26px}
.btn-light{position:absolute;left:515px;top:179px;width:170px;height:58px;background:#fff;color:var(--ink);font-size:16px}
.dots{position:absolute;top:370px;left:565px;display:flex;gap:8px}
.dots span{width:12px;height:12px;border:2px solid #fff;border-radius:50%}
.dots span.on{background:var(--red)}

/* heading */
.h2{font-family:var(--serif);font-weight:700;font-size:44px;color:var(--ink)}
.h2 em{font-style:normal;color:var(--red)}
.lead{font-size:16px;font-weight:500;line-height:26px;color:#333}

/* products */
.card{position:absolute;top:773px;width:217px;height:258px;background:var(--grey);padding:15px}
.card .photo{width:100%;height:100%;background:linear-gradient(180deg,#fafafa,#dcdcdc)}
.card-label{position:absolute;top:1048px;width:217px;text-align:center;font-family:var(--serif);font-size:14px;font-weight:600}
.arrow{position:absolute;top:881px;width:31px;height:31px;border-radius:50%;background:#555;display:flex;align-items:center;justify-content:center}
.arrow svg{width:12px;height:12px;stroke:#fff;stroke-width:3;fill:none}

/* about */
.about{top:1131px;left:0;width:1200px;height:518px;background:linear-gradient(90deg,#1b2530 0%,#6b3318 25%,#c9541a 45%,var(--orange) 58%,var(--orange) 100%)}
.about h2{position:absolute;left:631px;top:60px;font-family:var(--serif);font-size:44px;color:#fff}
.about p{position:absolute;left:631px;width:460px;font-size:15.5px;font-weight:600;line-height:29px;color:#fff}
.about .btn-light{left:631px;top:397px;width:171px;color:var(--red)}

/* faq */
.faq{position:absolute;width:480px;height:102px;background:#fff;border-radius:6px;box-shadow:0 3px 14px rgba(0,0,0,.12);display:flex;align-items:center;justify-content:space-between;padding:0 26px 0 28px;font-size:19.5px;font-weight:500;line-height:30px}
.faq .txt{width:390px}
.plus{width:19px;height:19px;border-radius:50%;background:var(--orange);position:relative;flex:none}
.plus::before,.plus::after{content:"";position:absolute;background:#fff;left:50%;top:50%;transform:translate(-50%,-50%)}
.plus::before{width:10px;height:2.5px}.plus::after{width:2.5px;height:10px}

/* touch band */
.touch{top:2226px;left:0;width:1200px;height:438px;background:linear-gradient(180deg,#0d0605 0%,#2a0c05 25%,#7a2a0a 55%,#d8601a 78%,#1a0804 100%)}
.touch h2{position:absolute;top:58px;font-family:var(--serif);font-size:44px;color:#fff}
.touch p{position:absolute;font-size:15.5px;font-weight:600;line-height:26px;color:#fff}
.soc{position:absolute;top:282px;width:40px;height:40px;border-radius:50%;background:#fff}
.soc::after{content:"";position:absolute;left:13px;top:13px;width:14px;height:14px;border-radius:50%;background:var(--red)}

/* footer */
.footer{top:2664px;left:0;width:1200px;height:456px;background:var(--dark);color:#fff}
.footer h3{position:absolute;top:74px;font-family:var(--serif);font-size:18px;font-weight:600}
.links{position:absolute;left:113px;top:118px;list-style:none;font-size:13px;font-weight:700}
.links li{height:33px}
.links li::before{content:"»";margin-right:12px}
.ci{position:absolute;left:281px;display:flex;align-items:center;gap:18px;font-size:13px;font-weight:700;line-height:17px}
.ci .ring{width:36px;height:36px;flex:none}
.ci .ring svg{fill:var(--red);width:16px;height:16px}
.field{position:absolute;background:#fff;border:1px solid #ccc;font-size:11px;color:#777;padding:8px 12px}
.btn-sub{position:absolute;left:970px;top:292px;width:116px;height:42px;background:linear-gradient(90deg,var(--orange),var(--red));color:#fff;font-size:13px}
.rule{position:absolute;left:111px;top:373px;width:978px;height:1px;background:#555}
.copy{position:absolute;left:111px;top:410px;font-size:12.5px}
.fsoc{position:absolute;top:405px;width:30px;height:30px;border-radius:50%;border:1.5px solid #fff}
.fsoc.red{background:var(--red)}
</style>
</head>
<body>

<div class="abs topbar">
  <div class="left"></div>
  <div class="item" style="left:105px">Follow Us On:
    <span class="ring sm"></span><span class="ring sm"></span><span class="ring sm"></span><span class="ring sm"></span>
  </div>
  <div class="item" style="left:432px">
    <span class="ring"><svg viewBox="0 0 24 24"><path d="M6.6 10.8a15 15 0 006.6 6.6l2.2-2.2a1 1 0 011-.25 11.4 11.4 0 003.6.6 1 1 0 011 1V20a1 1 0 01-1 1A17 17 0 013 4a1 1 0 011-1h3.5a1 1 0 011 1c0 1.25.2 2.45.6 3.6a1 1 0 01-.25 1z"/></svg></span>+1 555 014 2290</div>
  <div class="item" style="left:628px">
    <span class="ring"><svg viewBox="0 0 24 24"><path d="M3 5h18v14H3z M3 6l9 7 9-7" fill="none" stroke="#fff" stroke-width="2"/></svg></span>hello@ardentogrill.example</div>
  <div class="item" style="left:876px">
    <span class="ring"><svg viewBox="0 0 24 24"><path d="M12 2a7 7 0 00-7 7c0 5 7 13 7 13s7-8 7-13a7 7 0 00-7-7zm0 9.5A2.5 2.5 0 1112 6.5a2.5 2.5 0 010 5z"/></svg></span>Ardento, United States</div>
</div>

<header class="abs header">
  <div class="brand"><span class="dot"></span>ARDENTO</div>
  <nav class="nav">
    <a href="#" class="active" style="left:518px">HOME</a>
    <a href="#" style="left:614px">ABOUT</a>
    <a href="#" style="left:714px">PRODUCT</a>
    <a href="#" style="left:836px">REVIEWS</a>
  </nav>
  <a href="#" class="btn btn-cta">CONTACT US</a>
</header>

<section class="abs hero" role="img" aria-label="Kettle grill with open lid and flames rising from the grate">
  <h1 class="center">WELCOME TO ARDENTO</h1>
  <p class="center">Excepteur sint occaecat cupidatat non proident, sunt in culpa qui officia deserunt<br>mollit anim id est laborum.</p>
  <a href="#" class="btn btn-light">GET STARTED</a>
  <div class="dots"><span></span><span class="on"></span><span></span><span></span></div>
</section>

<h2 class="abs center h2" style="top:642px">OUR <em>PRODUCT</em></h2>
<p class="abs center lead" style="top:701px">Itaque earum rerum hic tenetur a sapiente delectus, ut aut reiciendis voluptatibus maiores alias consequatur aut<br>perferendis doloribus asperiores repellat.</p>

<div class="arrow" style="left:37px"><svg viewBox="0 0 12 12"><path d="M8 1L3 6l5 5"/></svg></div>
<div class="card" style="left:109px"><div class="photo" role="img" aria-label="Black ceramic kamado grill on legs"></div></div>
<div class="card" style="left:362px"><div class="photo" role="img" aria-label="Pair of grill claw tools"></div></div>
<div class="card" style="left:615px"><div class="photo" role="img" aria-label="Round portable charcoal grill"></div></div>
<div class="card" style="left:868px"><div class="photo" role="img" aria-label="Three-piece grilling utensil set"></div></div>
<div class="arrow" style="left:1123px"><svg viewBox="0 0 12 12"><path d="M4 1l5 5-5 5"/></svg></div>
<div class="card-label" style="left:109px">ARDENTO-13INCH-8</div>
<div class="card-label" style="left:362px">ARDENTO-15PCS-7</div>
<div class="card-label" style="left:615px">ARDENTO-13INCH-9</div>
<div class="card-label" style="left:868px">ARDENTO-3PC-1</div>

<section class="abs about" role="img" aria-label="Flames over a round charcoal grill grate">
  <h2>ABOUT ARDENTO</h2>
  <p style="top:114px">At vero eos et accusamus et iusto odio dignissimos ducimus qui blanditiis praesentium voluptatum deleniti atque corrupti quos dolores et quas molestias excepturi sint occaecati cupiditate non provident, similique sunt in culpa qui officia deserunt mollitia animi, id est laborum et dolorum fuga.</p>
  <p style="top:289px">Et harum quidem rerum facilis est et expedita distinctio. Nam libero tempore, cum soluta nobis est eligendi optio cumque nihil s voluptas assumenda est, omnis dolor repellendus.</p>
  <a href="#" class="btn btn-light">READ MORE</a>
</section>

<h2 class="abs center h2" style="top:1702px">FREQUENTLY <em>ASKED QUESTIONS</em></h2>
<div class="faq" style="left:110px;top:1780px"><span class="txt">Temporibus autem quibusdam et aut officiis debitis aut rerum necessitatibus?</span><span class="plus"></span></div>
<div class="faq" style="left:610px;top:1780px"><span class="txt">Nam libero tempore, cum soluta nobis est eligendi nihil impedit?</span><span class="plus"></span></div>
<div class="faq" style="left:110px;top:1909px"><span class="txt">Et harum quidem rerum facilis distinctio?</span><span class="plus"></span></div>
<div class="faq" style="left:610px;top:1909px"><span class="txt">Quis autem vel eum iure reprehenderit qui in ea volustiae?</span><span class="plus"></span></div>
<div class="faq" style="left:110px;top:2038px"><span class="txt">Itaque earum rerum hic tenetur a sapiente electus, ut aut reiciendis?</span><span class="plus"></span></div>
<div class="faq" style="left:610px;top:2038px"><span class="txt">Ut enim ad minima veniam, quis nostrum exercitationem ulosam?</span><span class="plus"></span></div>

<section class="abs touch" role="img" aria-label="Wall of glowing fire flames">
  <h2 class="center">GET IN TOUCH WITH US</h2>
  <p class="center" style="top:112px">Nemo enim ipsam voluptatem quia voluptas sit aspernatur aut odit aut fugit, sed quia consequuntur magni dolores eos<br>qui ratione voluptatem sequi nesciunt.</p>
  <p class="center" style="top:189px">Neque porro quisquam est, qui dolorem ipsum quia dolor sit amet, consectetur, adipisci velit, sed quia nonet dolore<br>magnam aliquam quaerat voluptatem.Ut enim ad minima veniam, quis nostrum exercitationem ullam corporis suscipit<br>laboriosam, nisi ut aliquid ex ea commodi consequatur.</p>
  <span class="soc" style="left:472px"></span><span class="soc" style="left:543px"></span><span class="soc" style="left:616px"></span><span class="soc" style="left:687px"></span>
</section>

<footer class="abs footer">
  <h3 style="left:113px">QUICK LINKS</h3>
  <h3 style="left:281px">CONTACT US</h3>
  <h3 style="left:595px">GET IN TOUCH:</h3>
  <ul class="links"><li>Home</li><li>About</li><li>Product</li><li>Services</li><li>Reviews</li></ul>
  <div class="ci" style="top:121px"><span class="ring"><svg viewBox="0 0 24 24"><path d="M12 2a7 7 0 00-7 7c0 5 7 13 7 13s7-8 7-13a7 7 0 00-7-7zm0 9.5A2.5 2.5 0 1112 6.5a2.5 2.5 0 010 5z"/></svg></span><span>123,Lorem ipsum dolor sit amet,<br>tetur adipiscing elit</span></div>
  <div class="ci" style="top:172px"><span class="ring"><svg viewBox="0 0 24 24"><path d="M6.6 10.8a15 15 0 006.6 6.6l2.2-2.2a1 1 0 011-.25 11.4 11.4 0 003.6.6 1 1 0 011 1V20a1 1 0 01-1 1A17 17 0 013 4a1 1 0 011-1h3.5a1 1 0 011 1c0 1.25.2 2.45.6 3.6a1 1 0 01-.25 1z"/></svg></span><span>Phone : +1 555 014 2290</span></div>
  <div class="ci" style="top:221px"><span class="ring"><svg viewBox="0 0 24 24"><path d="M3 5h18v14H3z"/><path d="M3 6l9 7 9-7" fill="none" stroke="#fff" stroke-width="2"/></svg></span><span>Email : hello@ardentogrill.example</span></div>
  <div class="field" style="left:596px;top:119px;width:240px;height:31px">Name :</div>
  <div class="field" style="left:846px;top:119px;width:240px;height:31px">Phone :</div>
  <div class="field" style="left:596px;top:164px;width:490px;height:30px">Email :</div>
  <div class="field" style="left:596px;top:206px;width:490px;height:70px">Message :</div>
  <a href="#" class="btn btn-sub">SUBMIT</a>
  <div class="rule"></div>
  <div class="copy">Copyrights © 2023 Ardento. All Rights Reserved.&nbsp; | &nbsp;Privacy policy</div>
  <span class="fsoc" style="left:985px"></span><span class="fsoc red" style="left:1023px"></span><span class="fsoc" style="left:1058px"></span>
</footer>

</body>
</html>
```